Bright Harbor Steady Yield Plan

I want a professional design for a new investment program that we have designed for prospecting new prospects. We have a company logo and the content that we would like for the brochure but we would like and design structure and graphics to help compliment the content. I am attaching a rough draft of the brochure that has some

Anyone looking for hard assets, inflation hedge, cash flow investments.

```html
<!DOCTYPE html>
<html lang="en">
<head>
<meta charset="utf-8">
<title>Bright Harbor Steady Yield Plan</title>
<link href="https://fonts.googleapis.com/css2?family=Montserrat:ital,wght@0,400;0,500;0,600;0,700;0,800;1,500;1,600;1,800;1,900&display=swap" rel="stylesheet">
<style>
:root{
  --navy:#2b3990;
  --ink:#1d1d2b;
  --paper:#f6f7fa;
  --backdrop:#bdbdbd;
  --rule:#2b3990;
}
*{box-sizing:border-box;margin:0;padding:0}
html,body{width:849px;height:1200px;overflow:hidden}
body{background:var(--backdrop);font-family:"Montserrat",sans-serif;color:var(--ink);position:relative}
.page{position:absolute;background:var(--paper);overflow:hidden;box-shadow:0 1px 3px rgba(0,0,0,.25)}
.p1{left:24px;top:42px;width:390px;height:552px}
.p2{left:435px;top:41px;width:392px;height:552px}
.p3{left:28px;top:621px;width:386px;height:562px}
.p4{left:435px;top:621px;width:388px;height:562px}
.abs{position:absolute}
.band{background:var(--navy);color:#fff}
.foot-bar{position:absolute;left:0;right:0;bottom:0;height:4px;background:var(--navy)}
.h-section{font-weight:900;font-style:italic;color:var(--navy);font-size:14px;line-height:15.8px;text-transform:uppercase;letter-spacing:-.1px}
.h-step{font-weight:800;font-style:italic;color:var(--navy);font-size:11px;text-transform:uppercase;margin-bottom:6px}
.underline{height:1.5px;background:var(--rule)}
ul.dots{list-style:none}
ul.dots li{position:relative;padding-left:13px;font-size:5.6px;line-height:7.8px;margin-bottom:5.6px;font-weight:500}
ul.dots li::before{content:"";position:absolute;left:0;top:2.4px;width:3.2px;height:3.2px;border-radius:50%;background:var(--navy)}
.band ul.dots li{color:#fff}
.band ul.dots li::before{background:#fff}
em.hl{color:var(--navy);font-style:italic;font-weight:600}
.photo{position:absolute}
ul.ticks{list-style:none}
ul.ticks li{position:relative;padding-left:13px;font-size:5.6px;line-height:7.8px;margin-bottom:3px;font-weight:500}
ul.ticks li svg{position:absolute;left:0;top:1px}
</style>
</head>
<body>

<section class="page p1">
  <header class="abs band" style="left:0;top:0;width:390px;height:48px;display:flex;align-items:center;justify-content:center">
    <h1 style="font-size:14px;font-weight:800;letter-spacing:.1px">BRIGHT HARBOR STEADY YIELD PLAN</h1>
  </header>
  <p class="abs" style="left:19px;top:63px;width:352px;font-size:8.2px;line-height:10px;text-align:center;font-weight:500">What should investors do to in this uncertain period to <span style="color:var(--navy);font-weight:600">profit from the evolving energy transition</span> and protect themselves from what appears to be an <span style="color:var(--navy);font-weight:600">inevitable wave of inflation?</span> We have one asset class and a business opportunity behind it that can address both.</p>
  <div class="photo" role="img" aria-label="Photo of signposts reading stocks, real estate, ETFs and mutual funds over a newspaper headline about where to invest your money" style="left:0;top:115px;width:390px;height:182px;background:linear-gradient(135deg,#8d8d8d,#d6d6d6 45%,#a3a3a3 75%,#5f5f5f)"></div>
  <div class="abs" style="left:19px;top:310px;width:353px;font-size:7.1px;line-height:9.85px;font-weight:500">
    <p style="margin-bottom:10px">Bright Harbor Minerals is a successful oil and gas mineral/royalty firm whose business model is to identify, acquire, manage, and divest energy royalty assets. Located in Maple Ridge, Texas, Bright Harbor's focus in the last 11 years has been on acquiring producing domestic energy royalty interests for our various partnerships, family offices, and individuals. Through years of hard work, we have developed the infrastructure to create outstanding royalty portfolios for these groups but have now adapted that to accommodate individuals outside of these structures. With the scale we have developed, we can manage the transactions inexpensively throughout the entire process and cut out middlemen and brokers who dilute investor returns. Basically, buy these legacy assets and transition them to investors at relatively the same price as industry buyers have for years.</p>
    <p>For this reason, we are providing an exclusive opportunity for a limited number of investors to participate in what we call our <em class="hl">Bright Harbor Steady Yield Plan</em>. This energy royalty program is designed for <em class="hl">non-industry investors</em> who want to own this kind of asset like experienced professionals in the energy industry have done for decades. The portfolio owners would own the assets with deeded title to the mineral interests in their name, not a partnership. Because we have a business structure to handle all facets of the process, we can make it turn-key for private personal portfolio owners. Investors get as much control as they like or can remain a passive investor similar to being in a partnership, the difference being owners in this structure can take control of their portfolio and/or liquidate at any time.</p>
  </div>
  <footer class="abs band" style="left:0;top:526px;width:390px;height:26px;display:flex;align-items:center;justify-content:center;font-size:12.5px;font-weight:500">www.brightharboryield.com</footer>
</section>

<section class="page p2">
  <h2 class="abs h-section" style="left:24px;top:40px;width:200px">What are personal portfolios?</h2>
  <div class="abs band" style="left:0;top:94px;width:392px;height:154px">
    <ul class="dots abs" style="left:22px;top:12px;width:152px">
      <li>They are a diverse portfolio of producing oil and gas mineral/royalty interests.</li>
      <li>Investors purchase a mineral deeded property that holds title to sub surface rights with current oil and gas production.</li>
      <li>Owners of these interest have no operational responsibility nor liability and maintain a passive position in the assets.</li>
      <li>These assets produce monthly cash flow from the sale of crude oil, natural gas, and NGL's by the operators that come from the existing wells and any new wells added to the position.</li>
    </ul>
    <div class="photo" role="img" aria-label="Illustration of oil pumpjacks standing on rising stacks of gold coins" style="left:187px;top:13px;width:183px;height:110px;background:linear-gradient(180deg,#ffffff 40%,#e9cf83 75%,#b88d2c)"></div>
    <ul class="dots abs" style="left:22px;top:130px;width:350px"><li>The assets are owned by the individual investor and are not part of a partnership, fund, or investment group.</li></ul>
  </div>
  <h2 class="abs h-section" style="left:75px;top:287px;width:295px;text-align:right">What owning a portfolio of energy royalties means for an investor?</h2>
  <div class="abs underline" style="left:78px;top:338px;width:292px"></div>
  <div class="photo" role="img" aria-label="Illustration of black oil barrels beside a stack of dollar bills in a spill of crude oil" style="left:21px;top:367px;width:185px;height:126px;background:radial-gradient(ellipse at 55% 65%,#4a4a4a,#cfcfcf 60%,#ffffff)"></div>
  <ul class="dots abs" style="left:218px;top:370px;width:153px">
    <li>It gives the owner an <em class="hl">investment in real assets</em>, deeded mineral acreage.</li>
    <li>The portfolio strategy is used to <em class="hl">avoid concentration</em> risk in that owners can diversify holdings by the type of producing commodity, formations, location, and operator.</li>
    <li>The investor gets <em class="hl">long term monthly cash flow</em> from all the production on the acreage.</li>
    <li>The investor has <em class="hl">no debt, liability, or capital calls</em> with owning royalties.</li>
    <li>The asset class is a <em class="hl">hedge against inflation</em>.</li>
    <li>The owner has <em class="hl">total control</em> over whether to hold, sell, or transfer the interests.</li>
  </ul>
  <div class="foot-bar"></div>
</section>

<section class="page p3">
  <h2 class="abs h-section" style="left:23px;top:38px;width:220px">Why Bright Harbor Minerals, LLC?</h2>
  <ul class="dots abs" style="left:23px;top:91px;width:200px">
    <li>Bright Harbor is a professional group who has operated successfully for over 11 years.</li>
    <li>Bright Harbor has developed a proprietary system for this asset class and has a team in place that manages the entire process for investors from A-Z.</li>
    <li>Through the development of our various partnerships, we now have a unique system that a small group of select individuals can take advantage of in the same way as larger groups and passively own an asset coveted by many industry professionals who have acquired energy royalties for decades.</li>
  </ul>
  <div class="abs" style="left:266px;top:88px;width:100px;height:90px;background:#fff;display:flex;flex-direction:column;align-items:center;justify-content:center;gap:6px">
    <span style="width:14px;height:14px;border-radius:50%;background:var(--navy)"></span>
    <span style="font-size:9px;font-weight:700;color:var(--navy);text-align:center;line-height:11px">BRIGHT HARBOR<br>MINERALS, LLC</span>
  </div>
  <h2 class="abs h-section" style="left:22px;top:199px;width:340px">Why did Bright Harbor create the Steady Yield Plan?</h2>
  <div class="abs underline" style="left:22px;top:236px;width:324px"></div>
  <div class="photo" role="img" aria-label="Photo of stacks of silver and gold coins with eyeglasses on a financial chart" style="left:20px;top:251px;width:344px;height:145px;background:linear-gradient(120deg,#dde3ea,#c9a45a 45%,#e8e2d0 70%,#b0b8c4)"></div>
  <ul class="dots abs" style="left:25px;top:418px;width:326px">
    <li>Bright Harbor's team acquires assets every month and allocates those acquisitions to the various entities under management according to their investment objectives and portfolio mix.</li>
    <li>Bright Harbor's strict acquisition guidelines only allows it to close on ~30% of the deals they evaluate. Despite the strict requirements, Bright Harbor has developed efficiencies in their system that has created some slack providing more acquisitions than the partnerships can absorb under their current capital structure.</li>
    <li>That leaves ~$2-$2.5 million per year in assets available, providing an opportunity for individuals to acquire producing royalty assets and take advantage of the <em class="hl">Bright Harbor Steady Yield Plan.</em></li>
    <li style="margin-top:9px">Because Bright Harbor has a team in place with a system to manage every aspect of the process, offering a turn-key option to select individual investors is a win, win solution for all parties.</li>
  </ul>
  <div class="foot-bar"></div>
</section>

<section class="page p4">
  <h2 class="abs h-section" style="left:23px;top:39px;width:300px">How does the Bright Harbor Steady Yield Plan work?</h2>
  <div class="abs underline" style="left:23px;top:79px;width:282px"></div>

  <div class="photo" role="img" aria-label="Graphic of a five step process cycle with numbered blue discs on a black background" style="left:231px;top:115px;width:135px;height:107px;background:radial-gradient(ellipse at 50% 50%,#3d63a8 0%,#1c2f55 40%,#000 75%)"></div>

  <div class="abs" style="left:23px;top:98px;width:200px">
    <h3 class="h-step">Identify</h3>
    <ul class="dots">
      <li>Bright Harbor has a proven, ongoing acquisition strategy with supporting infrastructure that acquires producing oil and gas mineral/royalty assets on a weekly basis.</li>
      <li>Bright Harbor holds these assets in its own portfolio for a limited period and transitions them to various partnerships or to individuals.</li>
    </ul>
  </div>
  <div class="abs" style="left:23px;top:190px;width:200px">
    <h3 class="h-step">Acquire</h3>
    <ul class="dots">
      <li>Steady Yield investors acquire a diverse group of producing energy royalties with a $50,000 minimum investment.</li>
      <li>The portfolio will be adapted to the investment objectives of the investor.</li>
    </ul>
  </div>
  <div class="abs" style="left:23px;top:277px;width:340px">
    <h3 class="h-step">Manage</h3>
    <ul class="dots">
      <li>Bright Harbor will manage the entire acquisition process from the legal documents, recording of title, notifying operators, notifying the taxing agencies, and transferring payments.</li>
      <li>Bright Harbor's affiliate royalty management company, <em class="hl">Linden Royalty Services, LLC</em>, will provide monthly cash flow statements, quarterly investment statements, and year end statistics and tax statements.</li>
    </ul>
  </div>
  <div class="abs" style="left:23px;top:359px;width:340px">
    <h3 class="h-step">Reinvestment</h3>
    <ul class="dots">
      <li>Throughout the year and in alignment with the investor's objectives, Bright Harbor will reinvest the cash flow from the initial portfolio into more royalty interests to increase the investor's asset base as well as their long-term cash flow.</li>
      <li>At some point, at the discretion of the owner/investor, Bright Harbor will stop the reinvestment plan and direct all monthly payments to go straight to the owner.</li>
    </ul>
  </div>
  <div class="abs" style="left:23px;top:450px;width:340px">
    <h3 class="h-step">Divestment</h3>
    <ul class="dots" style="margin-bottom:2px">
      <li>When/If the owner chooses to sell any or all their portfolio, Bright Harbor will assist them in the divestment by:</li>
    </ul>
    <ul class="ticks">
      <li><svg width="6" height="6" viewBox="0 0 6 6"><circle cx="3" cy="3" r="2.6" fill="none" stroke="#2b3990" stroke-width=".6"/><path d="M1.7 3l.9.9 1.7-1.8" fill="none" stroke="#2b3990" stroke-width=".6"/></svg>Providing the necessary data and documentation and advise them on various divestiture outlets.</li>
      <li><svg width="6" height="6" viewBox="0 0 6 6"><circle cx="3" cy="3" r="2.6" fill="none" stroke="#2b3990" stroke-width=".6"/><path d="M1.7 3l.9.9 1.7-1.8" fill="none" stroke="#2b3990" stroke-width=".6"/></svg>Set up the divestment for the seller with one or more outlets.</li>
      <li><svg width="6" height="6" viewBox="0 0 6 6"><circle cx="3" cy="3" r="2.6" fill="none" stroke="#2b3990" stroke-width=".6"/><path d="M1.7 3l.9.9 1.7-1.8" fill="none" stroke="#2b3990" stroke-width=".6"/></svg>Manage the sale process through funding.</li>
    </ul>
  </div>
  <div class="foot-bar"></div>
</section>

</body>
</html>
```